Health Clinic treating people with mental illness needs a website

We need a website for a new mental health clinic based in Florida called Solvane Wellness USA. We treat people with mental health issues such as depression, PTSD, Bipolar, chronic pain, etc. I want the website to be easy to follow and inviting to the visitors. It should be easy to locate the different treatment options and how to go about contacting and making appointments. The images on the website should be something that the patients can relate to, whether a close up of a woman's face, something that conveys emotion. The patients visiting this website are often sad and miserable, they need to be able to feel comfortable when they look at this website. I want them to feel that we understand where they are coming from. I like colors such as purple, turquoise, lavender.

Target Market(s)

College students, veterans, anyone with mental illness

Industry/Entity Type

Health And Wellness

Font styles to use
Serif
Sans Serif

Colors

Designer to choose colors to be used in the design.

Requirements
Must have
• There should be a home/landing page, about us page, treatment page, contact page, and a FAQ page. I've included my logo below.
Nice to have
• The flow of the web pages should be calming and welcoming. I want people to feel warm and understood when they enter our page.
Should not have
• The images and writing should not be overly stimulating or aggressive.

```html
<!DOCTYPE html>
<html lang="en">
<head>
<meta charset="utf-8">
<title>Solvane Wellness USA</title>
<link rel="stylesheet" href="https://fonts.googleapis.com/css2?family=Lato:wght@400;700;900&display=swap">
<style>
:root{
  --teal:#2ead91;
  --teal-light:#7ac8bb;
  --purple:#a5509e;
  --lavender:#c98ec3;
  --plum:#5c2a7a;
  --ink:#3d3d3d;
  --text:#4a4a4a;
  --panel:#f4f4f4;
  --rule:#cfcfcf;
}
*{box-sizing:border-box;margin:0;padding:0}
html,body{width:1200px;height:2949px;overflow:hidden;background:#fff}
body{position:relative;font-family:'Lato',sans-serif;color:var(--text)}
.abs{position:absolute}
.btn{position:absolute;background:var(--teal);color:#fff;font-weight:700;display:flex;align-items:center;justify-content:center;font-size:17px;letter-spacing:.2px}

/* header */
.topbar-contact{left:74px;top:56px;font-size:16px;color:var(--purple);display:flex;align-items:center;gap:8px;white-space:nowrap}
.topbar-contact svg{width:14px;height:14px;fill:var(--purple)}
.brand{left:450px;top:42px;width:300px;text-align:center;color:var(--plum);font-weight:700;font-size:30px;line-height:1}
.brand-sub{display:block;font-size:12px;letter-spacing:3px;margin-top:6px;color:var(--plum)}
.social{display:flex;gap:20px}
.social span{width:22px;height:22px;border-radius:50%;background:var(--purple);display:block}
.header-social{left:935px;top:56px}
.header-rule{left:74px;top:120px;width:1052px;height:1px;background:var(--rule)}
.nav{left:0;top:143px;width:1200px;display:flex;justify-content:center;gap:46px;font-size:15px;font-weight:700;color:var(--ink)}
.nav .active{color:var(--teal)}

/* hero */
.hero{left:0;top:181px;width:1200px;height:557px;background:linear-gradient(90deg,#9aa3b0 0%,#b4bcc6 45%,#cdb9a6 70%,#8fa7c3 100%)}
.hero-shade{left:0;top:181px;width:800px;height:557px;background:linear-gradient(90deg,rgba(120,128,142,.55),rgba(120,128,142,0))}
.hero-title{left:72px;top:352px;font-size:60px;font-weight:900;color:#fff;letter-spacing:.5px;line-height:68px}
.hero-text{left:75px;top:424px;width:680px;font-size:19px;line-height:31px;color:#fff;font-weight:700;white-space:nowrap}
.hero-btn{left:74px;top:507px;width:222px;height:48px}

/* about */
.about-photo{left:136px;top:835px;width:423px;height:392px;background:linear-gradient(135deg,#d9d4cc,#8b96a6 60%,#5f6672)}
.section-title{font-size:34px;font-weight:700;color:var(--ink);letter-spacing:.5px}
.about-title{left:614px;top:826px}
.about-text{left:614px;top:880px;width:520px;font-size:15px;line-height:31.5px;color:var(--ink);white-space:nowrap}
.about-text p+p{margin-top:11px}
.about-btn{left:614px;top:1180px;width:166px;height:47px}

/* treatment */
.treat-panel{left:74px;top:1346px;width:1052px;height:424px;background:var(--panel)}
.treat-title{left:0;top:1392px;width:1200px;text-align:center}
.treat-grid{left:100px;top:1459px;width:1002px;height:275px;display:flex}
.treat-card{flex:1;color:#fff;text-align:center;padding-top:40px}
.treat-card:nth-child(1){background:var(--teal)}
.treat-card:nth-child(2){background:var(--teal-light)}
.treat-card:nth-child(3){background:var(--purple)}
.treat-card:nth-child(4){background:var(--lavender)}
.treat-icon{width:64px;height:70px;margin:0 auto;background:rgba(255,255,255,.92);border-radius:32px 32px 10px 10px}
.treat-card h3{font-size:20px;font-weight:700;margin-top:28px;letter-spacing:.3px}
.treat-card p{font-size:15px;line-height:24px;margin:14px auto 0;width:210px;opacity:.95}

/* testimonials */
.testi-title{left:0;top:1820px;width:1200px;text-align:center}
.testi{top:1900px;width:320px;text-align:center}
.testi .quote{font-size:80px;line-height:70px;font-weight:900;color:var(--lavender);font-family:Georgia,serif;height:46px}
.testi h4{color:var(--teal);font-size:17px;font-weight:700;margin-top:12px}
.testi p{font-size:15px;line-height:26px;color:var(--ink);margin-top:10px}

/* contact */
.contact-panel{left:74px;top:2142px;width:527px;height:395px;background:var(--panel)}
.contact-title{left:74px;top:2170px;width:527px;text-align:center}
.contact-intro{left:74px;top:2222px;width:527px;text-align:center;font-size:15px;line-height:26px;color:var(--ink)}
.field{position:absolute;border-bottom:1px solid #b9b9b9;font-size:13px;color:var(--ink);padding-bottom:6px}
.contact-btn{left:247px;top:2448px;width:167px;height:47px}
.contact-photo{left:601px;top:2142px;width:525px;height:395px;background:linear-gradient(180deg,#8ea6c4 0%,#c7d3df 35%,#6f8a6e 62%,#3d4f4a 100%)}

/* footer */
.footer{left:74px;top:2590px;width:1052px;height:259px;background:var(--teal);color:#fff}
.footer h5{position:absolute;font-size:16px;font-weight:700;letter-spacing:.3px}
.footer-addr{position:absolute;left:30px;top:112px;font-size:15px;line-height:29px}
.footer-addr strong{font-size:16px;margin-left:3px}
.footer-links{position:absolute;left:295px;top:114px;width:250px;font-size:15px;line-height:29px;white-space:nowrap}
.footer-links svg{width:13px;height:13px;fill:#fff;margin-right:16px;vertical-align:-1px}
.footer-input{position:absolute;left:566px;top:125px;width:332px;height:42px;background:#fff;color:var(--ink);font-size:14px;display:flex;align-items:center;padding-left:16px;border:1px solid #ddd}
.footer-signup{position:absolute;left:912px;top:125px;width:90px;height:42px;background:var(--purple);font-size:15px;font-weight:700;display:flex;align-items:center;justify-content:center}
.footer-social{position:absolute;left:566px;top:193px}
.footer-social span{background:#fff}
.copyright{left:0;top:2885px;width:1200px;text-align:center;font-size:13px;color:var(--ink)}
</style>
</head>
<body>

<div class="abs topbar-contact">
  <svg viewBox="0 0 16 16"><path d="M3 1l3 3-2 2c1 2 3 4 5 5l2-2 3 3-2 3C7 15 1 9 0 3z"/></svg>
  941-555-0140 &nbsp;|&nbsp;
  <svg viewBox="0 0 16 16"><path d="M0 3h16v10H0zM1 4l7 5 7-5"/></svg>
  hello@solvane.example
</div>
<div class="abs brand">Solvane<span class="brand-sub">WELLNESS USA</span></div>
<div class="abs social header-social"><span></span><span></span><span></span><span></span><span></span></div>
<div class="abs header-rule"></div>
<nav class="abs nav"><span class="active">HOME</span><span>ABOUT ME</span><span>TREATMENT</span><span>FAQ</span><span>CONTACT</span></nav>

<div class="abs hero" role="img" aria-label="Close-up photo of a thoughtful woman resting her chin on her hand in a clinic room"></div>
<div class="abs hero-shade"></div>
<h1 class="abs hero-title">SOLVANE WELLNESS</h1>
<p class="abs hero-text">Sed ultrices nisl eu erat malesuada, ac scelerisque diam consectetur<br>vestibulum&nbsp; pretium turpis, laoreet feugiat metus tempus.</p>
<div class="btn hero-btn">BOOK APPOINTMENT</div>

<div class="abs about-photo" role="img" aria-label="Photo of two women talking on a sofa during a counselling session"></div>
<h2 class="abs section-title about-title">ABOUT US</h2>
<div class="abs about-text">
  <p>Aenean eget sagittis dolor. Vestibulum sit amet ornare nibh.<br>Donec porta sapien ac metus maximus ullamcorper. In eget sagittis ex.<br>Nulla viverra volutpat tempus. Mauris ut volutpat ante, quis sollicitudin<br>ante. Proin gravida enim eget dolor tincidunt, in laoreet odio aliquet.<br>cursus, dui sit amet blandit lacinia, tellus libero lobortis ante, a laoreet<br>metus diam tincidunt nunc. Ut eu velit est.</p>
  <p>Aenean volutpat leo vel bibendum dignissim. Nulla vel auctor quam.<br>Nulla facilisi. Praesent at tellus nec enim tincidunt tristique a vel turpis.</p>
</div>
<div class="btn about-btn">READ MORE</div>

<div class="abs treat-panel"></div>
<h2 class="abs section-title treat-title">TREATMENT</h2>
<div class="abs treat-grid">
  <div class="treat-card"><div class="treat-icon" role="img" aria-label="Illustration of a person sitting with head in hands"></div><h3>DEPRESSION</h3><p>Nullam viverra vestibulum pretium. Integer bibendum ullamcorper nulla.</p></div>
  <div class="treat-card"><div class="treat-icon" role="img" aria-label="Illustration of a person in distress"></div><h3>PTSD</h3><p>Nullam viverra vestibulum pretium. Integer bibendum ullamcorper nulla.</p></div>
  <div class="treat-card"><div class="treat-icon" role="img" aria-label="Illustration of two facing head profiles"></div><h3>BIPOLAR</h3><p>Nullam viverra vestibulum pretium. Integer bibendum ullamcorper nulla.</p></div>
  <div class="treat-card"><div class="treat-icon" role="img" aria-label="Illustration of a head with pain marks"></div><h3>CHRONIC PAIN</h3><p>Nullam viverra vestibulum pretium. Integer bibendum ullamcorper nulla.</p></div>
</div>

<h2 class="abs section-title testi-title">TESTIMONIALS</h2>
<div class="abs testi" style="left:80px"><div class="quote">&ldquo;</div><h4>MARIA .L</h4><p>Cras eleifend nunc enim, eu placerat odio ultrices ac. Integer id nulla leo a ante auctor, eleifend arcu eget..</p></div>
<div class="abs testi" style="left:441px"><div class="quote">&ldquo;</div><h4>MARIA .L</h4><p>Cras eleifend nunc enim, eu placerat odio ultrices ac. Integer id nulla leo a ante auctor, eleifend arcu eget..</p></div>
<div class="abs testi" style="left:802px"><div class="quote">&ldquo;</div><h4>MARIA .L</h4><p>Cras eleifend nunc enim, eu placerat odio ultrices ac. Integer id nulla leo a ante auctor, eleifend arcu eget..</p></div>

<div class="abs contact-panel"></div>
<h2 class="abs section-title contact-title">CONTACT US</h2>
<p class="abs contact-intro">Cras eleifend nunc enim, eu placerat odio<br>ultrices ac&nbsp; sed egestas lorem.</p>
<div class="field" style="left:95px;top:2296px;width:222px">Name</div>
<div class="field" style="left:342px;top:2296px;width:222px">Name</div>
<div class="field" style="left:95px;top:2330px;width:469px;padding-bottom:12px">Email Address</div>
<div class="field" style="left:95px;top:2371px;width:469px;padding-bottom:44px">Message</div>
<div class="btn contact-btn">SUBMIT</div>
<div class="abs contact-photo" role="img" aria-label="Photo of waterfront high-rise buildings with palm trees and boats"></div>

<footer class="abs footer">
  <h5 style="left:29px;top:77px">CONTACT ME</h5>
  <div class="footer-addr"><strong>Solvane Wellness</strong><br>1480 Harbor View Lane<br>Suite 210<br>Sarasota, Florida 34236</div>
  <div class="footer-links">
    <div><svg viewBox="0 0 16 16"><path d="M3 1l3 3-2 2c1 2 3 4 5 5l2-2 3 3-2 3C7 15 1 9 0 3z"/></svg>Tel (941) 555-0172</div>
    <div><svg viewBox="0 0 16 16"><path d="M0 3h16v10H0z"/></svg>Email hello@solvane.example</div>
    <div style="font-weight:700">Book a Appointment</div>
  </div>
  <h5 style="left:566px;top:77px">SUBSCRIBE TO GET MY NEWSLETTER</h5>
  <div class="footer-input">Enter Email Address</div>
  <div class="footer-signup">SIGN UP</div>
  <div class="social footer-social"><span></span><span></span><span></span><span></span><span></span></div>
</footer>
<p class="abs copyright">Copyright &copy; 2019 Solvane Wellness USA All Rights Reserved</p>

</body>
</html>
```